Website Banner Redesign for Kelvra Cargo Depot

Business Name:
KELVRA CARGO DEPOT

About Us:
- We’re a proudly Australian company that designs and builds tough, reliable toolboxes for Utes, Trucks, and Campervans. Our products are made to handle harsh conditions and are trusted by tradies, off-roaders, and professional fleets across the country.

Project Goal:
- We want to refresh our homepage and category banners with bold, modern designs that better showcase our products and value proposition.

Why We’re Updating:
Our current banners show the products well, but we want to improve:
Visual impact and hierarchy
- Readability of text (especially on mobile)
- Clearer calls-to-action (CTAs)
- Brand messaging around “Built Tough”, “Aussie Made”, and “Custom Fit-Outs”

Target Audience:
- Tradespeople
- 4x4 & off-road enthusiasts
- Caravan & camping community
- Ute/Truck/Caravan dealerships
- Fleet and commercial buyers

Design Style We Want:
- Bold, confident, rugged
- Clean layout with clear focal points
- Strong product imagery (we’ll supply photos)
- Use of brand colors: Black, White, Red, Grey
- Professional, not too busy or cluttered

Banner Uses:
- Homepage hero banner
- Category landing pages

UTE TOOLBOXES - https://www.kelvracargo.com.au/aluminium-toolboxes/
Truck Boxes - https://www.kelvracargo.com.au/truck-toolboxes/
Canopies - https://www.kelvracargo.com.au/canopy/
Dog Boxes - https://www.kelvracargo.com.au/dog-boxes/
CAMPER BOXES - https://www.kelvracargo.com.au/camper-toolboxes/
Accessories - https://www.kelvracargo.com.au/accessories/

- Can be reused for desktop and mobile

Inspiration Style:
Think: 4x4 accessory brands, tough tradie gear, or clean eCommerce landing banners from premium auto suppliers.

Target Market(s)

All in Brief Above

Industry/Entity Type

Retail

Requirements
Must have
• A banner using our products only. A banner for each category, and 2 alternate banners for the home page.
Nice to have
• I have added some designs which i like..... Please take a look and take inspiration from them.

```html
<!DOCTYPE html>
<html lang="en">
<head>
<meta charset="utf-8">
<title>Versatile Camper Boxes – Kelvra Cargo Depot</title>
<link href="https://fonts.googleapis.com/css2?family=Anton&family=Bebas+Neue&display=swap" rel="stylesheet">
<style>
  :root {
    --bg-deep: #182226;
    --bg-mid: #2c3b41;
    --bg-glow: #5d6f75;
    --white: #ffffff;
    --yellow: #ffd200;
    --cta: #a61c4b;
    --box-white-hi: #f2f3f3;
    --box-white-lo: #c9cccc;
    --box-black-hi: #3a3d40;
    --box-black-lo: #151618;
  }
  * { margin: 0; padding: 0; box-sizing: border-box; }
  html, body { width: 900px; height: 1200px; overflow: hidden; }
  body { background: var(--bg-deep); }
  .banner {
    position: relative;
    width: 900px;
    height: 1200px;
    overflow: hidden;
    background:
      radial-gradient(ellipse 420px 300px at 560px 640px, var(--bg-glow) 0%, rgba(93,111,117,0) 100%),
      radial-gradient(ellipse 700px 600px at 380px 300px, #3a4b51 0%, rgba(58,75,81,0) 100%),
      linear-gradient(180deg, var(--bg-mid) 0%, var(--bg-deep) 100%);
  }
  .headline {
    position: absolute;
    left: 106px;
    top: 58px;
    font-family: "Anton", sans-serif;
    font-weight: 400;
    font-size: 128px;
    line-height: 158px;
    letter-spacing: 6px;
    color: var(--white);
    text-transform: uppercase;
    white-space: nowrap;
  }
  .product {
    position: absolute;
    border-radius: 6px;
  }
  .product--carrier {
    left: 101px; top: 504px; width: 209px; height: 288px;
    background: linear-gradient(160deg, var(--box-white-hi) 0%, var(--box-white-lo) 100%);
  }
  .product--toolbox {
    left: 356px; top: 500px; width: 480px; height: 292px;
    background: linear-gradient(160deg, var(--box-black-hi) 0%, var(--box-black-lo) 100%);
  }
  .tagline {
    position: absolute;
    left: 111px;
    top: 822px;
    font-family: "Bebas Neue", sans-serif;
    font-size: 88px;
    line-height: 79px;
    color: var(--yellow);
    text-transform: uppercase;
    white-space: nowrap;
  }
  .cta {
    position: absolute;
    left: 107px;
    top: 1015px;
    width: 367px;
    height: 125px;
    border-radius: 20px;
    background: var(--cta);
    color: var(--white);
    font-family: "Bebas Neue", sans-serif;
    font-size: 88px;
    line-height: 125px;
    text-decoration: none;
    padding-left: 57px;
  }
</style>
</head>
<body>
  <main class="banner">
    <h1 class="headline">Versatile<br>Camper<br>Boxes</h1>

    <div class="product product--carrier" role="img" aria-label="Photo of a white powder-coated gas bottle holder with slotted sides"></div>

    <div class="product product--toolbox" role="img" aria-label="Photo of a black camper toolbox with lid open and mounting flanges"></div>

    <p class="tagline">Ideal storage solutions<br>for your adventures</p>

    <a class="cta" href="https://www.kelvracargo.com.au/camper-toolboxes/">EXPLORE</a>
  </main>
</body>
</html>
```